We want to revamp our current website -www.kelvota-eng.com

We need to have a new website for our company that offers non-destructive and testing solutions around Africa. We have a current website but it does not fulfil our needs as it is:<br/>1. Not clear and bright<br/>2. Does not fit well in mobile <br/>3. Is not easily updatable by our staff. <br/>4. Is not linked to our social media sites.<br/>We would like to have a website that addresses the above issues. Our colours are Red and Blue and should communicate to our clients, that we are a professional company open for business, ready to solve their non-destructive testing problems around Africa. * Helpful if it is a wordpress website.

Target Market(s)

Our customers are B2B Corporate clients. We mainly work in
1. Storage Terminals
2. Refineries
3. Oil and Gas offshore and onshore rigs.

Industry/Entity Type

Oil And Gas

Contact Information for Business Card

Please find our current business card on the uploaded files.

Coding

Coded - Design and coding required

Number of Pages Required

5+ page

Font styles to use
Serif
Sans Serif

Requirements
Must have
• I like this site www.pirelo-inspection.com They are in the same industry.
• I don't understand how to call them but all the 'call to action' buttons, and links to our Social media pages.
• Must have a place where we update information in a regular basis. A Blog!

```html
<!DOCTYPE html>
<html lang="en">
<head>
<meta charset="utf-8">
<title>Kelvota Engineering</title>
<link href="https://fonts.googleapis.com/css2?family=Archivo:wght@400;500;600;700&display=swap" rel="stylesheet">
<style>
:root{
  --navy:#1f2a5e;
  --navy-dark:#18214d;
  --red:#a51c24;
  --red-bright:#c4262e;
  --ink:#2b2b33;
  --muted:#55565f;
  --paper:#ffffff;
  --mist:#f4f2f3;
  --footer:#222224;
  --footer-text:#d6d6da;
}
*{box-sizing:border-box;margin:0;padding:0}
html,body{width:1200px;height:4781px;overflow:hidden}
body{font-family:"Archivo",sans-serif;color:var(--ink);background:var(--paper);position:relative}
section,header,footer,nav{position:absolute;left:0;width:1200px}
.abs{position:absolute}
.btn{position:absolute;display:flex;align-items:center;justify-content:center;background:var(--red);color:#fff;font-weight:600;text-transform:uppercase;letter-spacing:.5px;text-decoration:none}
.rule{position:absolute;height:3px;width:44px;background:var(--red)}
.section-title{position:absolute;left:0;width:1200px;text-align:center;font-weight:700;font-size:31px;letter-spacing:.5px;text-transform:uppercase}

/* header */
.site-header{top:0;height:89px;background:#fff}
.brand{position:absolute;display:flex;align-items:center;gap:10px}
.brand-mark{width:54px;height:54px;border-radius:50%;background:var(--red)}
.brand-name{font-size:38px;font-weight:500;color:var(--navy);line-height:1}
.brand-sub{font-size:10px;color:var(--navy);letter-spacing:.5px;text-transform:uppercase}
.follow-label{left:644px;top:37px;font-size:13px;font-weight:600;color:var(--navy)}
.social-dot{width:29px;height:29px;border-radius:50%;background:var(--navy)}
.call-label{left:859px;top:24px;font-size:12px;font-weight:600;color:var(--navy)}
.call-number{left:859px;top:40px;font-size:22px;font-weight:700;color:var(--red)}

.main-nav{top:89px;height:45px;background:var(--navy)}
.main-nav a{position:absolute;top:0;height:45px;line-height:45px;font-size:12.5px;font-weight:600;color:#fff;text-decoration:none;text-transform:uppercase;letter-spacing:.3px}
.main-nav a.active{background:var(--red);padding:0 11px}

/* hero */
.hero{top:134px;height:565px;background:linear-gradient(160deg,#6f6a5c 0%,#4d4236 35%,#2e2a27 60%,#55483a 100%)}
.hero-title{left:132px;top:178px;font-size:45px;line-height:51px;font-weight:700;color:#fff;letter-spacing:2px;text-transform:uppercase}
.hero .btn{left:137px;top:359px;width:141px;height:49px;font-size:17px;border:2px solid #fff}
.dots{left:550px;top:516px;display:flex;gap:11px}
.dots span{width:9px;height:9px;border-radius:50%;background:#fff}
.dots span.on{background:var(--red);box-shadow:0 0 0 2px #fff}

/* welcome */
.welcome{top:699px;height:540px;background:#fff}
.kicker{left:132px;top:56px;font-size:20px;font-weight:700;color:var(--navy)}
.welcome-title{left:130px;top:84px;font-size:37px;font-weight:700;color:var(--red);letter-spacing:.5px}
.welcome-copy{left:132px;top:166px;width:470px;font-size:15px;line-height:21px;color:var(--ink)}
.welcome-copy p+p{margin-top:21px}
.welcome .btn{left:132px;top:436px;width:123px;height:40px;font-size:14px}
.welcome-photo{left:651px;top:70px;width:416px;height:416px;border-radius:50%;background:radial-gradient(circle at 40% 35%,#3c4c86,#222a5a 65%,#161c40)}

/* services */
.services{top:1239px;height:529px;background:linear-gradient(120deg,#243066,#1f2a5e 60%,#263368)}
.services .section-title{top:54px;color:#fff}
.services .rule{left:578px;top:108px;background:#fff}
.service-card{position:absolute;top:158px;width:291px;height:315px;background:#fff;text-align:center}
.service-card svg{position:absolute;left:113px;top:24px}
.service-card h3{position:absolute;left:0;top:112px;width:100%;font-size:20px;line-height:24px;color:var(--navy);text-transform:uppercase;font-weight:700}
.service-card p{position:absolute;left:40px;top:177px;width:211px;font-size:13px;line-height:17px;color:var(--muted)}
.service-card .btn{left:96px;top:255px;width:99px;height:27px;font-size:12px}

/* HSE */
.hse{top:1768px;height:584px;background:#fff}
.hse-frame{left:130px;top:61px;width:938px;height:445px;border:2px solid var(--navy)}
.hse-photo{left:0;top:0;width:447px;height:441px;background:linear-gradient(150deg,#6b7d86 0%,#7a5a45 45%,#5a3a2c 100%)}
.hse-title{left:504px;top:44px;font-size:31px;line-height:37px;font-weight:700;color:var(--navy);text-transform:uppercase}
.hse-copy{left:504px;top:161px;width:360px;font-size:16px;line-height:23px;color:var(--ink)}
.hse .btn{left:506px;top:355px;width:121px;height:41px;font-size:15px}

/* values */
.values{top:2352px;height:583px;background:#eeedf0;overflow:hidden}
.values-photo{left:0;top:0}
.values-title{left:132px;top:48px;font-size:31px;font-weight:700;color:var(--navy);text-transform:uppercase}
.values .rule{left:132px;top:92px}
.value-item{position:absolute;left:132px;width:440px}
.value-icon{position:absolute;left:4px;top:0;width:70px;height:70px;border-radius:50%;background:var(--red);border:4px solid #fff;box-shadow:0 0 0 2px var(--red)}
.value-icon svg{position:absolute;left:13px;top:13px}
.value-item h4{position:absolute;left:96px;top:0;font-size:14.5px;font-weight:700;color:var(--navy);text-transform:uppercase}
.value-item p{position:absolute;left:96px;top:24px;width:332px;font-size:12px;line-height:16px;color:var(--muted)}

/* blog */
.blog{top:2935px;height:621px;background:#fff}
.blog .section-title{top:60px;color:var(--navy)}
.blog .rule{left:578px;top:111px}
.post{position:absolute;top:166px;width:291px;height:379px;background:#fff;box-shadow:0 4px 18px rgba(20,25,60,.14)}
.post-photo{position:absolute;left:0;top:0;width:291px;height:195px}
.post h3{position:absolute;left:27px;top:225px;font-size:14.5px;font-weight:700;color:var(--navy);text-transform:uppercase}
.post p{position:absolute;left:27px;top:253px;width:235px;font-size:12px;line-height:15px;color:var(--muted)}
.post .btn{left:28px;top:321px;width:87px;height:26px;font-size:10px}

/* resources */
.resources{top:3556px;height:534px;background:linear-gradient(120deg,#243066,#1f2a5e 60%,#263368)}
.resources .section-title{top:48px;color:#fff}
.resources .rule{left:578px;top:100px}
.resource-box{left:130px;top:154px;width:938px;height:323px;background:#fff}
.resource-copy{left:41px;top:48px;width:338px;font-size:15.5px;line-height:21px;color:var(--ink)}
.resources .btn{left:44px;top:241px;width:112px;height:35px;font-size:14px}
.resource-photo{left:417px;top:0;width:521px;height:323px;background:linear-gradient(140deg,#6d7a86 0%,#3d4a57 45%,#8a8f95 70%,#b0782e 100%)}

/* clients */
.clients{top:4090px;height:284px;background:var(--mist)}
.clients .section-title{top:54px;color:var(--navy)}
.clients .rule{left:578px;top:104px}
.client{position:absolute;top:186px;display:flex;align-items:center;gap:7px;font-size:19px;font-weight:700;color:#50545e}
.client .sq{width:14px;height:14px;background:#50545e}
.arrow{position:absolute;top:190px}

/* footer */
.site-footer{top:4374px;height:407px;background:var(--footer);color:var(--footer-text)}
.site-footer .brand-name,.site-footer .brand-sub{color:#fff}
.footer-head{position:absolute;top:58px;font-size:14px;font-weight:700;color:#fff;text-transform:uppercase}
.footer-menu{position:absolute;left:469px;top:101px;list-style:none;font-size:13px;line-height:24px;text-transform:uppercase}
.contact-row{position:absolute;display:flex;gap:14px;font-size:13px;line-height:18px}
.contact-row .ico{flex:none;width:30px;height:30px;border-radius:50%;display:flex;align-items:center;justify-content:center}
.ico.red{background:var(--red)}
.ico.white{background:#fff}
.copyright{position:absolute;left:0;top:340px;width:1200px;text-align:center;font-size:11px;color:var(--footer-text)}
</style>
</head>
<body>

<header class="site-header">
  <div class="brand" style="left:132px;top:16px">
    <div class="brand-mark"></div>
    <div><div class="brand-name">kelvota</div><div class="brand-sub">Engineering</div></div>
  </div>
  <span class="abs follow-label">FOLLOW</span>
  <span class="abs social-dot" style="left:713px;top:31px" aria-label="Friendline page"></span>
  <span class="abs social-dot" style="left:752px;top:31px" aria-label="Worknet page"></span>
  <svg class="abs" style="left:818px;top:30px" width="32" height="32" viewBox="0 0 24 24" aria-hidden="true"><path fill="var(--navy)" d="M6.6 10.8c1.4 2.8 3.8 5.1 6.6 6.6l2.2-2.2c.3-.3.7-.4 1-.2 1.1.4 2.3.6 3.6.6.6 0 1 .4 1 1V20c0 .6-.4 1-1 1C10.6 21 3 13.4 3 4c0-.6.4-1 1-1h3.5c.6 0 1 .4 1 1 0 1.3.2 2.5.6 3.6.1.3 0 .7-.2 1L6.6 10.8z"/></svg>
  <span class="abs call-label">CALL US</span>
  <span class="abs call-number">+254 20 418 3390/2</span>
</header>

<nav class="main-nav">
  <a class="active" style="left:126px">Home</a>
  <a style="left:210px">About Us</a>
  <a style="left:321px">Inspection</a>
  <a style="left:453px">NDT Services</a>
  <a style="left:588px">Advanced NDT Services</a>
  <a style="left:803px">Engineering Services</a>
  <a style="left:1006px">Contact</a>
</nav>

<section class="hero" role="img" aria-label="Photo of a buried steel pipeline with yellow valves on an excavated site">
  <h1 class="abs hero-title">We offer inspection<br>&amp; engineering<br>services</h1>
  <a class="btn">Read More</a>
  <div class="abs dots"><span></span><span></span><span class="on"></span><span></span><span></span></div>
</section>

<section class="welcome">
  <div class="abs kicker">WELCOME TO</div>
  <h2 class="abs welcome-title">KELVOTA ENGINEERING</h2>
  <div class="abs welcome-copy">
    <p>With roots at the Kenyan coast, we have over 10 years' experience in NDT, Mechanical Engineering and Marine Services. We enjoy a presence in the larger East and Central African region. Our head office is located in Mombasa with our workshop at Ridgeview, from where we offer our wide array of services.</p>
    <p>Our operations are split into two divisions - Kelvota Inspection Services and Kelvota Engineering Services. We pick the best talents in the industry and have heavily invested in developing our staff's skills further through rigorous internal and external training in keeping up with industry trends.</p>
  </div>
  <a class="btn">Read More</a>
  <div class="abs welcome-photo" role="img" aria-label="Circular photo of technicians at work on site"></div>
</section>

<section class="services">
  <h2 class="section-title">Our Services</h2>
  <div class="rule"></div>

  <article class="service-card" style="left:132px">
    <svg width="66" height="66" viewBox="0 0 66 66" aria-hidden="true"><g fill="var(--red)"><path d="M18 22a15 15 0 0 1 30 0z"/><rect x="15" y="21" width="36" height="4" rx="2"/><circle cx="33" cy="31" r="9"/><path d="M10 64c0-14 10-22 23-22s23 8 23 22z"/></g><path d="M33 44l-4 8 4 10 4-10z" fill="#fff"/></svg>
    <h3>Training<br>Institute</h3>
    <p>Lorem Ipsum is simply dummy text of the printing and type setting industry</p>
    <a class="btn">Read More</a>
  </article>

  <article class="service-card" style="left:454px">
    <svg width="66" height="66" viewBox="0 0 66 66" aria-hidden="true"><g fill="none" stroke="var(--red)" stroke-width="4"><path d="M14 6h30l10 10v46H14z"/><circle cx="32" cy="26" r="11"/><path d="M40 34l10 10"/><path d="M22 48h24M22 55h24"/></g></svg>
    <h3>Inspection<br>Services</h3>
    <p>Lorem Ipsum is simply dummy text of the printing and type setting industry</p>
    <a class="btn">Read More</a>
  </article>

  <article class="service-card" style="left:777px">
    <svg width="66" height="66" viewBox="0 0 66 66" aria-hidden="true"><g fill="none" stroke="var(--red)" stroke-width="4"><path d="M4 56h58"/><path d="M10 56V30h10v26M28 56V18h10v38M46 56V10h12v46"/><path d="M20 38h8M38 30h8"/></g></svg>
    <h3>Pipeline<br>Services</h3>
    <p>Lorem Ipsum is simply dummy text of the printing and type setting industry</p>
    <a class="btn">Read More</a>
  </article>
</section>

<section class="hse">
  <div class="abs hse-frame">
    <div class="abs hse-photo" role="img" aria-label="Photo of a worker in orange coveralls and harness inspecting a storage tank roof"></div>
    <h2 class="abs hse-title">Our Health, Safety &amp;<br>Enviromental Policy</h2>
    <p class="abs hse-copy">We are 100% compliant with the requirements of the national safety directorate and other international safety standards. Our need for providing a safe enviroment supersedes our need for revenue maximisation, hence our commitment to providing an injury and incident free work area.</p>
    <a class="btn">Read More</a>
  </div>
</section>

<section class="values">
  <svg class="abs values-photo" width="1200" height="583" viewBox="0 0 1200 583" role="img" aria-label="Red-tinted photo of large pipes inside a plant">
    <defs><linearGradient id="valuesTint" x1="0" y1="0" x2="1" y2="1"><stop offset="0" stop-color="#a3242c"/><stop offset=".55" stop-color="#8a1c24"/><stop offset="1" stop-color="#b4343a"/></linearGradient></defs>
    <polygon points="581,0 1200,0 1200,583 642,583" fill="url(#valuesTint)"/>
  </svg>
  <h2 class="abs values-title">Our Values</h2>
  <div class="rule"></div>

  <div class="value-item" style="top:155px">
    <div class="value-icon"><svg width="36" height="36" viewBox="0 0 36 36" aria-hidden="true"><circle cx="18" cy="18" r="8" fill="none" stroke="#fff" stroke-width="4"/><g stroke="#fff" stroke-width="4"><path d="M18 2v6M18 28v6M2 18h6M28 18h6M6.7 6.7l4.2 4.2M25.1 25.1l4.2 4.2M6.7 29.3l4.2-4.2M25.1 10.9l4.2-4.2"/></g></svg></div>
    <h4>Passion for innovation</h4>
    <p>Our customer is at the centre of all innovation. We encourage innovation not only in products and services but also in processes, human resources, management and business models.</p>
  </div>

  <div class="value-item" style="top:290px">
    <div class="value-icon"><svg width="36" height="36" viewBox="0 0 36 36" aria-hidden="true"><circle cx="18" cy="12" r="8" fill="#fff"/><path d="M3 36c0-10 7-15 15-15s15 5 15 15z" fill="#fff"/></svg></div>
    <h4>Customer obsession</h4>
    <p>The wants, wishes and views of our customers guide our every action. We are curious about our customers and continually aim to learn more about them and their needs. We keep our promises.</p>
  </div>

  <div class="value-item" style="top:426px">
    <div class="value-icon"><svg width="36" height="36" viewBox="0 0 36 36" aria-hidden="true"><g fill="#fff"><rect x="3" y="24" width="6" height="10"/><rect x="12" y="19" width="6" height="15"/><rect x="21" y="14" width="6" height="20"/><rect x="30" y="8" width="5" height="26"/></g><path d="M3 17L14 9l6 4L33 3" fill="none" stroke="#fff" stroke-width="3"/></svg></div>
    <h4>Drive for results</h4>
    <p>We strive for a visible, measurable and balanced benefit from everything we do. We focus on the essential and aim at the simple, informal, lean and direct ways of doing things.</p>
  </div>
</section>

<section class="blog">
  <h2 class="section-title">Latest Blog</h2>
  <div class="rule"></div>

  <article class="post" style="left:132px">
    <div class="post-photo" role="img" aria-label="Close-up photo of a corroded red-painted bolt with green leaves" style="background:linear-gradient(135deg,#6f8a3a,#8a4a5a 50%,#3d3a3a)"></div>
    <h3>Lorem Ipsum is simply dum</h3>
    <p>Sed ut perspiciatis unde omnis iste natus error sit voluptatem accusa ntium doloremque.</p>
    <a class="btn">Read More</a>
  </article>

  <article class="post" style="left:454px">
    <div class="post-photo" role="img" aria-label="Photo of a measuring tape on a green cutting mat" style="background:linear-gradient(135deg,#2f5a66,#2a4a58 55%,#c9b070)"></div>
    <h3>Lorem Ipsum is simply dum</h3>
    <p>Sed ut perspiciatis unde omnis iste natus error sit voluptatem accusa ntium doloremque.</p>
    <a class="btn">Read More</a>
  </article>

  <article class="post" style="left:777px">
    <div class="post-photo" role="img" aria-label="Photo of an ultrasonic testing probe beside a monitor display" style="background:linear-gradient(135deg,#6a5a3a,#8a7048 50%,#5a4a7a)"></div>
    <h3>Lorem Ipsum is simply dum</h3>
    <p>Sed ut perspiciatis unde omnis iste natus error sit voluptatem accusa ntium doloremque.</p>
    <a class="btn">Read More</a>
  </article>
</section>

<section class="resources">
  <h2 class="section-title">Our Resources</h2>
  <div class="rule"></div>
  <div class="abs resource-box">
    <p class="abs resource-copy">To deliver on our promise of quality and reliability to our clients, we have invested in the best equipment to produce accurate and timely results. Additionally, we have a fully equiped laboratory to carry out extensive tests as well as a workshop. Our computerized systems are also instrumental in delivering real-time and precise outcomes.</p>
    <a class="btn">Read More</a>
    <div class="abs resource-photo" role="img" aria-label="Photo of a worker in a green helmet cutting steel plate with a torch"></div>
  </div>
</section>

<section class="clients">
  <h2 class="section-title">Our Clients</h2>
  <div class="rule"></div>
  <svg class="arrow" style="left:74px" width="16" height="26" viewBox="0 0 16 26" aria-hidden="true"><path d="M13 2L3 13l10 11" fill="none" stroke="#8a8c94" stroke-width="2.5"/></svg>
  <div class="client" style="left:142px"><span class="sq"></span>Harcon</div>
  <div class="client" style="left:282px">Velmora</div>
  <div class="client" style="left:450px">Tristek</div>
  <div class="client" style="left:628px">Ambrel Logistics</div>
  <div class="client" style="left:822px">Norvane</div>
  <div class="client" style="left:982px">Sulvo Energy</div>
  <svg class="arrow" style="left:1113px" width="16" height="26" viewBox="0 0 16 26" aria-hidden="true"><path d="M3 2l10 11L3 24" fill="none" stroke="#8a8c94" stroke-width="2.5"/></svg>
</section>

<footer class="site-footer">
  <div class="brand" style="left:132px;top:108px">
    <div class="brand-mark"></div>
    <div><div class="brand-name">kelvota</div><div class="brand-sub">Engineering</div></div>
  </div>

  <div class="footer-head" style="left:469px">Menu</div>
  <ul class="footer-menu">
    <li>Home</li><li>About Us</li><li>Services</li><li>Products</li><li>Blog</li><li>Contact Us</li>
  </ul>

  <div class="footer-head" style="left:656px">Contact Us</div>
  <div class="contact-row" style="left:654px;top:102px">
    <span class="ico red"><svg width="12" height="16" viewBox="0 0 12 16" aria-hidden="true"><path d="M6 0a6 6 0 0 1 6 6c0 4-6 10-6 10S0 10 0 6a6 6 0 0 1 6-6z" fill="#fff"/><circle cx="6" cy="6" r="2" fill="var(--red)"/></svg></span>
    <span>Harbour Row, Coral Lane<br>P.O. BOX 40562-80100</span>
  </div>
  <div class="contact-row" style="left:654px;top:164px">
    <span class="ico red"><svg width="14" height="14" viewBox="0 0 24 24" aria-hidden="true"><path fill="#fff" d="M6.6 10.8c1.4 2.8 3.8 5.1 6.6 6.6l2.2-2.2c.3-.3.7-.4 1-.2 1.1.4 2.3.6 3.6.6.6 0 1 .4 1 1V20c0 .6-.4 1-1 1C10.6 21 3 13.4 3 4c0-.6.4-1 1-1h3.5c.6 0 1 .4 1 1 0 1.3.2 2.5.6 3.6.1.3 0 .7-.2 1z"/></svg></span>
    <span>Call Us<br>+ 254 20 418 3391/2</span>
  </div>
  <div class="contact-row" style="left:654px;top:226px">
    <span class="ico red"><svg width="14" height="11" viewBox="0 0 14 11" aria-hidden="true"><rect width="14" height="11" rx="1" fill="#fff"/><path d="M1 1l6 5 6-5" fill="none" stroke="var(--red)" stroke-width="1.5"/></svg></span>
    <span>E mail Us<br>info@kelvota-eng.com</span>
  </div>

  <div class="footer-head" style="left:942px">Follow Us</div>
  <div class="contact-row" style="left:940px;top:102px"><span class="ico white"></span><span>Like us on<br>FRIENDLINE</span></div>
  <div class="contact-row" style="left:940px;top:164px"><span class="ico white"></span><span>Follow us on<br>CHIRPLY</span></div>
  <div class="contact-row" style="left:940px;top:226px"><span class="ico white"></span><span>Follow us on<br>WORKNET</span></div>

  <div class="copyright">Copyright © 2020 All Rights Reserved</div>
</footer>

</body>
</html>
```